I'm looking for a smart new design for business cards

Industry/Entity Type

Commercial Electrical

Contact Information for Business Card

Logo, name, email, position, website QR

Requirements
Nice to have
• Logo embedded behind the text side

```html
<!DOCTYPE html>
<html lang="en">
<head>
<meta charset="utf-8">
<title>Harbourline Electrical – Business Card</title>
<link rel="stylesheet" href="https://fonts.googleapis.com/css2?family=Montserrat:wght@400;500;700;800&display=swap">
<style>
  :root {
    --backdrop: #999999;
    --brand-red: #dd1c2c;
    --brand-red-light: #e8404e;
    --brand-red-deep: #a5141f;
    --brand-navy: #2b2c7a;
    --ink: #1b1b1b;
    --text-grey: #3a3a3a;
    --card-white: #ffffff;
  }
  * { margin: 0; padding: 0; box-sizing: border-box; }
  html, body {
    width: 1200px;
    height: 1108px;
    overflow: hidden;
    background: var(--backdrop);
    font-family: "Montserrat", sans-serif;
  }
  .canvas { position: relative; width: 1200px; height: 1108px; }

  .card {
    position: absolute;
    left: 242px;
    width: 715px;
    height: 408px;
    border-radius: 36px;
    overflow: hidden;
  }

  /* Front */
  .card-front {
    top: 119px;
    background:
      linear-gradient(115deg,
        rgba(255,255,255,0) 0%,
        rgba(255,255,255,0) 38%,
        rgba(255,255,255,0.16) 46%,
        rgba(255,255,255,0.10) 62%,
        rgba(255,255,255,0) 80%),
      var(--brand-red);
  }
  .front-mark {
    position: absolute;
    inset: 0;
    display: flex;
    flex-direction: column;
    align-items: center;
    justify-content: center;
    gap: 14px;
  }
  .front-mark-dot {
    width: 64px;
    height: 64px;
    border-radius: 50%;
    background: var(--brand-red-deep);
    opacity: 0.55;
  }
  .front-mark-name {
    font-weight: 800;
    font-size: 44px;
    line-height: 1.1;
    letter-spacing: 1px;
    text-align: center;
    color: var(--brand-red-deep);
    opacity: 0.75;
  }

  /* Back */
  .card-back {
    top: 580px;
    background: var(--card-white);
  }
  .brand-block {
    position: absolute;
    left: 40px;
    top: 150px;
    width: 300px;
    display: flex;
    align-items: center;
    justify-content: center;
    gap: 14px;
  }
  .brand-dot {
    flex: none;
    width: 34px;
    height: 34px;
    border-radius: 50%;
    background: var(--brand-red);
  }
  .brand-name {
    font-weight: 800;
    font-size: 28px;
    line-height: 1.1;
    letter-spacing: 0.5px;
    color: var(--brand-navy);
  }
  .divider {
    position: absolute;
    left: 370px;
    top: 95px;
    width: 2px;
    height: 221px;
    background: var(--brand-red);
  }
  .details {
    position: absolute;
    left: 400px;
    top: 90px;
    color: var(--text-grey);
  }
  .person-name {
    font-weight: 700;
    font-size: 35px;
    line-height: 1;
    color: var(--brand-navy);
    letter-spacing: -0.3px;
  }
  .person-name .surname { color: var(--brand-red); }
  .person-role {
    margin-top: 10px;
    font-size: 19px;
    font-weight: 500;
  }
  .address {
    margin-top: 18px;
    font-size: 19px;
    font-weight: 500;
    line-height: 29px;
  }
  .contact-list {
    list-style: none;
    margin-top: 12px;
    font-size: 19px;
    font-weight: 500;
  }
  .contact-list li {
    display: flex;
    align-items: center;
    gap: 9px;
    height: 28.5px;
  }
  .contact-icon { width: 16px; height: 16px; flex: none; }
</style>
</head>
<body>
<main class="canvas">

  <section class="card card-front" aria-label="Card front">
    <div class="front-mark">
      <span class="front-mark-dot"></span>
      <span class="front-mark-name">HARBOURLINE<br>ELECTRICAL</span>
    </div>
  </section>

  <section class="card card-back" aria-label="Card back">
    <div class="brand-block">
      <span class="brand-dot"></span>
      <span class="brand-name">HARBOURLINE<br>ELECTRICAL</span>
    </div>

    <div class="divider"></div>

    <div class="details">
      <h1 class="person-name">Daniel <span class="surname">Hartley</span></h1>
      <p class="person-role">Managing Director</p>
      <p class="address">Your address, City<br>State, Zip 1234</p>
      <ul class="contact-list">
        <li>
          <svg class="contact-icon" viewBox="0 0 16 16" aria-hidden="true">
            <path fill="#dd1c2c" d="M1 6c0-2 3-3.5 7-3.5S15 4 15 6v1.2h-3.5V5.6H4.5v1.6H1z"/>
            <path fill="#dd1c2c" d="M3.5 8.5L5 6.8h6l1.5 1.7V14h-9z"/>
          </svg>
          <span>123 456 789</span>
        </li>
        <li>
          <svg class="contact-icon" viewBox="0 0 16 16" aria-hidden="true">
            <rect x="1" y="3.5" width="14" height="9.5" fill="#dd1c2c"/>
            <path d="M1.5 4l6.5 5 6.5-5M1.5 12.5l5-4.3M14.5 12.5l-5-4.3" stroke="#fff" stroke-width="1.2" fill="none"/>
          </svg>
          <span>info@yourgmail.com</span>
        </li>
        <li>
          <svg class="contact-icon" viewBox="0 0 16 16" aria-hidden="true">
            <circle cx="8" cy="8" r="7" fill="#dd1c2c"/>
            <path d="M1 8h14M8 1c-2.5 2.5-2.5 11.5 0 14M8 1c2.5 2.5 2.5 11.5 0 14" stroke="#fff" stroke-width="1" fill="none"/>
          </svg>
          <span>www.yourwebsite.com</span>
        </li>
      </ul>
    </div>
  </section>

</main>
</body>
</html>
```